Create modern and sleek business card for luxury real estate company

We're a "boutique" real estate office looking for a design that gets across a highly modern luxury brand. Blacks and whites are probably the best colors unless we try a silver foil for the logo. I've attached a version of our current logo here. I'd like to swap out the current font on there with Gotham Light Regular.

I'm looking to have one side of the card have the logo with the space for our agents info on the other side.

Target Market(s)

Young professionals in a "luxury" headspace

Industry/Entity Type

Real estate

Contact Information for Business Card

A place for agent name, cell number, website. The slogan "Simply Rethinking Real Estate".

Font styles to use
Other font styles liked:
• Gotham Regular

Colors

Designer to choose only greyscale colors for use in the design.

Requirements
Must have
• Matte black as the background color. Clean lines and use of contrast. A specific design aspect that will use silver foil.
Nice to have
• Up in the air on integrating a QR code
Should not have
• Any houses or other real estate related design (ex: a clip art house)

```html
<!DOCTYPE html>
<html lang="en">
<head>
<meta charset="utf-8">
<title>Halden Estates – Business Card</title>
<link href="https://fonts.googleapis.com/css2?family=Libre+Baskerville:wght@400;700&family=Arimo:wght@400&display=swap" rel="stylesheet">
<style>
  :root {
    --backdrop: #2a2a2a;
    --card-black: #0c0c0c;
    --card-edge: #1a1a1a;
    --ink-white: #f2f2f2;
    --ink-soft: #d6d6d6;
    --divider: #2c2c2c;
  }
  * { margin: 0; padding: 0; box-sizing: border-box; }
  html, body {
    width: 1200px; height: 900px; overflow: hidden;
    background: var(--backdrop);
  }
  .stage {
    width: 1200px; height: 900px;
    display: flex; align-items: center; justify-content: center; gap: 40px;
  }
  .card {
    width: 540px; height: 308px;
    background: var(--card-black);
    border: 1px solid var(--card-edge);
    position: relative;
    color: var(--ink-white);
  }
  .brand {
    display: flex; flex-direction: column; align-items: center; gap: 16px;
  }
  .brand-circle {
    width: 62px; height: 62px; border-radius: 50%;
    border: 2px solid var(--ink-white);
  }
  .brand-name {
    font-family: "Libre Baskerville", serif;
    font-weight: 400;
    color: var(--ink-white);
    text-transform: uppercase;
    letter-spacing: 1px;
    text-align: center;
    line-height: 1.15;
  }
  /* info side */
  .card-info .brand {
    position: absolute; left: 0; top: 0; width: 48%; height: 100%;
    justify-content: center;
  }
  .card-info .brand-name { font-size: 30px; }
  .card-info .divider {
    position: absolute; left: 48%; top: 28px; bottom: 28px;
    width: 1px; background: var(--divider);
  }
  .agent {
    position: absolute; left: 53%; top: 58px; right: 16px;
    font-family: "Arimo", sans-serif;
  }
  .agent-name {
    font-family: "Libre Baskerville", serif; font-weight: 700;
    font-size: 18px; letter-spacing: 1px; text-transform: uppercase;
  }
  .agent-title { font-size: 14px; color: var(--ink-soft); margin-top: 2px; }
  .contact-list { list-style: none; margin-top: 16px; }
  .contact-list li {
    display: flex; align-items: center; gap: 8px;
    font-size: 15px; line-height: 24px;
  }
  .contact-list svg { width: 15px; height: 15px; flex: none; }
  .address { margin-top: 14px; font-size: 15px; line-height: 20px; padding-left: 23px; }
  /* logo side */
  .card-logo { display: flex; align-items: center; justify-content: center; }
  .card-logo .brand { flex-direction: row; gap: 20px; }
  .card-logo .brand-circle { width: 72px; height: 72px; }
  .card-logo .brand-name { font-size: 32px; text-align: left; }
</style>
</head>
<body>
<main class="stage">
  <section class="card card-info">
    <div class="brand">
      <span class="brand-circle"></span>
      <span class="brand-name">Halden<br>Estates</span>
    </div>
    <span class="divider"></span>
    <div class="agent">
      <p class="agent-name">Marcus Ellery</p>
      <p class="agent-title">Managing Director</p>
      <ul class="contact-list">
        <li>
          <svg viewBox="0 0 16 16" fill="none" stroke="#f2f2f2" stroke-width="1.4"><path d="M4 2l2.5 3-1.5 1.5c.8 1.8 2.2 3.2 4 4L10.5 9l3 2.5-1.5 2C7 13.5 2.5 9 2.5 3.5z"/></svg>
          055-310 842 617
        </li>
        <li>
          <svg viewBox="0 0 16 16" fill="none" stroke="#f2f2f2" stroke-width="1.4"><rect x="1.5" y="3.5" width="13" height="9"/><path d="M1.5 3.5L8 9l6.5-5.5"/></svg>
          hello@haldenestates.com
        </li>
        <li>
          <svg viewBox="0 0 16 16" fill="none" stroke="#f2f2f2" stroke-width="1.2"><circle cx="8" cy="8" r="6.5"/><ellipse cx="8" cy="8" rx="3" ry="6.5"/><path d="M1.5 8h13M2.5 5h11M2.5 11h11"/></svg>
          www.haldenestates.com
        </li>
      </ul>
      <p class="address">18, Marlowe Crescent Lane<br>30217, Northvale</p>
    </div>
  </section>

  <section class="card card-logo">
    <div class="brand">
      <span class="brand-circle"></span>
      <span class="brand-name">Halden<br>Estates</span>
    </div>
  </section>
</main>
</body>
</html>
```